VELMOR Website Design

We need a website designed for our company VELMOR. We are a luxury lifestyle club that will provide benefits and services for our members. The site should be clean & sleek, preferably using black and white (or darker colors). (example sites: stravenhall.example, plinth.example)

Here is a link of a sample page I did using wix. (https://dunmere7.sitehostly.example/mysite) This can be used to get a general idea.

Target Market(s)

Upper Middle Class in the United States

Number of Pages Required

5+ page

Font styles to use
Sans Serif
Other font styles liked:
• Arial (or other similar fonts)

Requirements
Must have
• A clean design that is eye-catching and speaks to our company.
Nice to have
• Ideas for copy.

```html
<!DOCTYPE html>
<html lang="en">
<head>
<meta charset="utf-8">
<title>VELMOR — A Members Only Lifestyle Club</title>
<link href="https://fonts.googleapis.com/css2?family=Arimo:ital,wght@0,400;0,700;1,400&display=swap" rel="stylesheet">
<style>
:root{
  --black:#000;
  --charcoal:#222;
  --white:#fff;
  --muted:#cfcfcf;
  --rule:#8a8a8a;
}
*{box-sizing:border-box;margin:0;padding:0}
html,body{width:1200px;height:3727px;overflow:hidden;background:var(--black);color:var(--white);font-family:"Arimo",Arial,sans-serif}
.page{position:relative;width:1200px;height:3727px}
section,footer{position:absolute;left:0;width:1200px;overflow:hidden}
.abs{position:absolute}
.center{left:0;width:1200px;text-align:center}
.btn{position:absolute;left:519px;width:164px;height:45px;border:2px solid var(--white);color:var(--white);font-size:13px;display:flex;align-items:center;justify-content:center}
.section-title{font-size:28px;font-weight:700;letter-spacing:.5px}
.title-rule{position:absolute;left:555px;width:90px;height:2px;background:var(--white)}
.dots{display:flex;gap:6px;justify-content:center}
.dots span{width:7px;height:7px;border-radius:50%;background:var(--white)}

/* hero */
.hero{top:0;height:641px}
.hero-photo{position:absolute;inset:0;background:
  radial-gradient(ellipse at 22% 55%,rgba(150,85,30,.75),transparent 45%),
  radial-gradient(ellipse at 78% 30%,rgba(120,60,25,.7),transparent 40%),
  linear-gradient(160deg,#3a2a2c 0%,#2a1c22 40%,#4a3326 70%,#221a1e 100%)}
.hero-shade{position:absolute;inset:0;background:rgba(20,12,20,.35)}
.lang{left:119px;top:8px;font-size:12px;display:flex;align-items:center;gap:6px}
.login{left:1030px;top:8px;font-size:12px;display:flex;align-items:center;gap:6px}
.brand{top:16px;font-size:40px;font-weight:700;letter-spacing:1px}
.nav{top:73px;display:flex;justify-content:center;gap:28px;font-size:12px}
.hero-headline{top:284px;font-size:41px;font-weight:700;text-shadow:0 2px 6px rgba(0,0,0,.5)}
.hero-sub{top:332px;font-size:13px}
.slider-dots{top:586px}
.slider-dots span{width:11px;height:11px}
.slider-dots span.active{background:transparent;border:2px solid var(--white)}

/* about */
.about{top:641px;height:293px;background:var(--charcoal)}
.about-body{left:154px;top:107px;width:892px;font-size:12.5px;line-height:20px;text-align:center;color:var(--white)}

/* services */
.services{top:934px;height:1078px;background:var(--black)}
.services-intro-title{top:140px;font-size:19px;font-weight:700}
.services-intro{top:174px;font-size:12.5px;line-height:22px}
.service{position:absolute;width:300px;text-align:center}
.service-photo{width:214px;height:214px;border-radius:50%;margin:0 auto}
.service-name{margin-top:32px;font-size:19px;font-weight:700;letter-spacing:.3px}

/* newsletter */
.newsletter{top:2012px;height:765px;background:var(--charcoal)}
.post{position:absolute;top:166px;width:312px}
.post-photo{width:312px;height:234px}
.post-cat{margin-top:14px;font-size:12px}
.post-title{margin-top:14px;font-size:13px;font-weight:700;line-height:17px;text-transform:uppercase}
.post-excerpt{margin-top:12px;font-size:12px;line-height:15.5px}
.post .dots{justify-content:flex-start;margin-top:10px}

/* contact */
.contact{top:2777px;height:457px;background:var(--black)}
.field{position:absolute;border-bottom:2px solid var(--rule);height:28px;font-size:12.5px;font-style:italic;padding-left:4px}

/* subscribe */
.subscribe{top:3234px;height:219px;background:var(--charcoal)}
.subscribe-text{top:50px;font-size:17px;font-weight:700;line-height:23px;letter-spacing:.3px}
.sub-input{left:363px;top:124px;width:335px;height:45px;border:2px solid var(--white);font-size:13px;font-style:italic;padding:14px 0 0 14px}
.sub-send{left:703px;top:124px;width:134px;height:45px;background:var(--white);color:var(--black);font-size:13px;display:flex;align-items:center;justify-content:center}

/* footer */
.footer{top:3453px;height:274px;background:var(--black)}
.footer-brand{top:42px;font-size:38px;font-weight:700;letter-spacing:1px}
.footer-nav{top:104px;display:flex;justify-content:center;gap:26px;font-size:12px}
.social{top:150px;display:flex;justify-content:center;gap:30px}
.social span{width:18px;height:18px;border-radius:50%;background:var(--white)}
.footer-rule{left:122px;top:202px;width:956px;height:1px;background:#555}
.copyright{top:230px;font-size:12px}
</style>
</head>
<body>
<div class="page">

  <section class="hero">
    <div class="hero-photo" role="img" aria-label="Members raising glasses of wine and beer in a toast"></div>
    <div class="hero-shade"></div>
    <div class="abs lang">
      <svg width="12" height="12" viewBox="0 0 12 12"><circle cx="6" cy="6" r="5" fill="none" stroke="#fff" stroke-width="1.3"/><path d="M1 6h10M6 1c-3 3-3 7 0 10M6 1c3 3 3 7 0 10" fill="none" stroke="#fff" stroke-width="1"/></svg>EN
    </div>
    <div class="abs login">
      <svg width="12" height="12" viewBox="0 0 12 12"><path d="M2 10L10 2M5 2h5v5" fill="none" stroke="#fff" stroke-width="1.6"/></svg>Login
    </div>
    <div class="abs center brand">VELMOR</div>
    <nav class="abs center nav"><span>Home</span><span>About</span><span>Services &amp; Benefits</span><span>Noted</span><span>Contact</span></nav>
    <h1 class="abs center hero-headline">A MEMBERS ONLY LIFESTYLE CLUB</h1>
    <p class="abs center hero-sub">Lorem Ipsum is simply dummy text of the printing and typesetting industry</p>
    <div class="btn" style="top:372px">Learn More</div>
    <div class="abs center dots slider-dots"><span class="active"></span><span></span><span></span></div>
  </section>

  <section class="about">
    <h2 class="abs center section-title" style="top:44px">ABOUT US</h2>
    <p class="abs about-body">Lorem Ipsum is simply dummy text of the printing and typesetting industry. Lorem Ipsum has been the industry's standard dummy text ever since the 1500s, when an unknown printer took a galley of type and scrambled it to make a type specimen book. It has survived not only five centuries, but also the leap into electronic typesetting, remaining essentially unchanged. It was popularised in the 1960s with the release of Lettrapress sheets containing Lorem Ipsum passages, and more recently with desktop publishing software like Quillset Layout including versions of Lorem Ipsum.</p>
    <div class="abs center dots" style="top:238px"><span></span><span></span><span></span></div>
  </section>

  <section class="services">
    <h2 class="abs center section-title" style="top:47px;font-size:26px">SERVICES &amp; BENIFTS</h2>
    <div class="title-rule" style="top:99px"></div>
    <h3 class="abs center services-intro-title">WE ARE VELMOR</h3>
    <p class="abs center services-intro">Built in the image of a"Multi-Family Office", VELMOR provides members with access to just about any service, experience, and event desirable.<br>VELMOR is truly the most exclusive lifestyle club out there.</p>
    <div class="btn" style="top:236px">Apply For Membership</div>

    <div class="service" style="left:155px;top:333px"><div class="service-photo" role="img" aria-label="Hands working a calculator over paperwork" style="background:linear-gradient(135deg,#e8e4de,#8a8580 60%,#c7a56d)"></div><div class="service-name">ACCOUNTING SERVICES</div></div>
    <div class="service" style="left:446px;top:333px"><div class="service-photo" role="img" aria-label="Blue stock market ticker board" style="background:linear-gradient(135deg,#6a86c8,#20305e 60%,#0e1a3a)"></div><div class="service-name">INVESTMENT SERVICES</div></div>
    <div class="service" style="left:742px;top:333px"><div class="service-photo" role="img" aria-label="Judge's gavel beside a hand signing documents" style="background:linear-gradient(135deg,#f0eee9,#b59a7a 55%,#5a3f2a)"></div><div class="service-name">LAWYER SERVICES</div></div>

    <div class="service" style="left:155px;top:641px"><div class="service-photo" role="img" aria-label="Modern residential building under a clear sky" style="background:linear-gradient(180deg,#dfe6ec,#b7b2a2 55%,#5b6b3e)"></div><div class="service-name">REAL ESTATE SERVICES</div></div>
    <div class="service" style="left:446px;top:641px"><div class="service-photo" role="img" aria-label="Concierge service bell on a hotel desk" style="background:radial-gradient(circle at 50% 70%,#c9a060,#6b4a2a 45%,#2a1c14)"></div><div class="service-name">24/7 CONCIERGE</div></div>
    <div class="service" style="left:742px;top:641px"><div class="service-photo" role="img" aria-label="Private jet on the tarmac with a waiting car" style="background:linear-gradient(180deg,#e8ecf0,#b9c0c6 55%,#2a2c30)"></div><div class="service-name">PRIVATE JET TRAVEL</div></div>

    <div class="btn" style="top:976px">View All Services</div>
  </section>

  <section class="newsletter">
    <h2 class="abs center section-title" style="top:57px">NEWSLETTER</h2>
    <div class="title-rule" style="top:109px"></div>

    <article class="post" style="left:122px">
      <div class="post-photo" role="img" aria-label="Couple with luggage watching a plane from an airport window" style="background:linear-gradient(180deg,#c8d4de,#8a969e 60%,#4a4a4c)"></div>
      <div class="post-cat">Lifestyle, Travel</div>
      <div class="post-title">How Ashbury Club's revamp<br>has elevated the golfing lifestyle</div>
      <p class="post-excerpt">Lorem Ipsum is simply dummy text of the printing and typesetting industry. Lorem Ipsum has been the industry's standard dummy text ever since the 1500s.</p>
      <div class="dots"><span></span><span></span><span></span></div>
    </article>

    <article class="post" style="left:447px">
      <div class="post-photo" role="img" aria-label="Aerial view of a sandy bay with turquoise water" style="background:linear-gradient(160deg,#3aa6b8,#6cc4c8 40%,#d8c8a0 60%,#5c6a3a)"></div>
      <div class="post-cat">Travel</div>
      <div class="post-title">A heavenly experience on Turkey</div>
      <p class="post-excerpt">Lorem Ipsum is simply dummy text of the printing and typesetting industry. Lorem Ipsum has been the industry's standard dummy text ever since the 1500s.</p>
      <div class="dots"><span></span><span></span><span></span></div>
    </article>

    <article class="post" style="left:768px">
      <div class="post-photo" role="img" aria-label="Banquet hall lit in purple for a private event" style="background:radial-gradient(ellipse at 50% 70%,#d24ad8,#6a1a7a 50%,#2a0a34)"></div>
      <div class="post-cat">Events</div>
      <div class="post-title">Decoration for private events</div>
      <p class="post-excerpt">Lorem Ipsum is simply dummy text of the printing and typesetting industry. Lorem Ipsum has been the industry's standard dummy text ever since the 1500s.</p>
      <div class="dots"><span></span><span></span><span></span></div>
    </article>

    <div class="btn" style="top:636px">View More</div>
  </section>

  <section class="contact">
    <h2 class="abs center section-title" style="top:62px">CONTACT US</h2>
    <div class="title-rule" style="top:117px"></div>
    <div class="field" style="left:268px;top:176px;width:206px">Name</div>
    <div class="field" style="left:497px;top:176px;width:206px">Email Address</div>
    <div class="field" style="left:723px;top:176px;width:208px">Phone Number</div>
    <div class="field" style="left:268px;top:248px;width:663px">Message</div>
    <div class="btn" style="top:330px">Submit</div>
  </section>

  <section class="subscribe">
    <p class="abs center subscribe-text">SUBSCRIBE TO THE LATEST NEWS AND EXPERIENCES IN<br>GLOBAL LUXURY, CONTEMPORARY CULTURE, AND EXCLUSIVE OFFERS</p>
    <div class="abs sub-input">Email Address</div>
    <div class="abs sub-send">Send</div>
  </section>

  <footer class="footer">
    <div class="abs center footer-brand">VELMOR</div>
    <nav class="abs center footer-nav"><span>Home</span><span>About</span><span>Services &amp; Benefits</span><span>Noted</span><span>Contact</span></nav>
    <div class="abs center social" aria-label="Social links"><span></span><span></span><span></span><span></span><span></span></div>
    <div class="abs footer-rule"></div>
    <p class="abs center copyright">© Copyright 2018 Velmor. All Right Reserved</p>
  </footer>

</div>
</body>
</html>
```